New Web Site Design - Tallow Ridge Communication Solutions

We are looking for a completely new web site design. Tallow Ridge Communication Solutions is a full service company providing PBX and IP/Cloud Based phone systems. We also sell and install video camera surveillance systems and provide low voltage cabling services (CAT5 and CAT3). We are looking for something professional looking. We want to be able to showcase our vendor partners as well as be able to show photos of some of the work we have done. We will also want to be able to post PDF brochures as well as make changes to the website ourselves.

Target Market(s)

Commercial

Industry/Entity Type

Communication

Coding

Coded - Design and coding required

Number of Pages Required

5+ page

Font styles to use
Sans Serif

Colors
0455a3

Requirements
Must have
• Ability to upload PDF brochures
• Professional look and feel
• Ability to upload and easily insert job photos
• Thinking it should have at least 6 pages: Main page, phone systems and services page, carrier services page, video surveillance systems and service page, low voltage cabling services page, contact us page

```html
<!DOCTYPE html>
<html lang="en">
<head>
<meta charset="utf-8">
<title>Tallow Ridge Communication Solutions</title>
<link href="https://fonts.googleapis.com/css2?family=Roboto+Condensed:wght@400;700&family=Roboto:wght@400;500&family=Noto+Serif&display=swap" rel="stylesheet">
<style>
:root{
  --brand:#0455a3;
  --brand-dark:#0b2c55;
  --ink:#333;
  --muted:#555;
  --rule:#cfcfcf;
  --map:#3d3f42;
  --panel:rgba(125,128,132,.55);
  --field:rgba(160,163,167,.45);
  --bar:#8c8d8f;
  --white:#fff;
}
*{margin:0;padding:0;box-sizing:border-box}
html,body{width:1134px;height:1200px;overflow:hidden;background:var(--white)}
body{position:relative;font-family:Roboto,Arial,sans-serif;color:var(--ink)}
.abs{position:absolute}
.cond{font-family:"Roboto Condensed",Arial,sans-serif}

/* header */
.header{left:0;top:0;width:1134px;height:136px;background:var(--white)}
.side-band{top:0;height:136px;background:var(--brand)}
.brand-mark{left:74px;top:25px;width:92px;height:92px;border-radius:50%;background:var(--white)}
.brand-mark::after{content:"";position:absolute;left:9px;top:9px;width:74px;height:74px;border-radius:50%;background:var(--brand-dark)}
.brand-name{left:164px;top:50px;color:var(--brand);font-weight:400;line-height:1}
.brand-name .l1{display:block;font-size:28px}
.brand-name .l2{display:block;font-size:15px;margin-top:4px;letter-spacing:.2px}
.follow{left:845px;top:22px;font-size:12.5px;color:#222}
.social{top:15px;width:28px;height:28px;border-radius:50%;background:#3a3a3a}
.brochure-btn{left:688px;top:88px;width:185px;height:28px;background:var(--brand);color:var(--white);font-size:17px;line-height:28px;padding-left:14px}
.call-label{left:922px;top:76px;font-size:14px;color:#222}
.call-number{left:922px;top:92px;font-size:21px;color:var(--brand)}

/* nav */
.nav{left:0;top:136px;width:1134px;height:48px;background:var(--brand);border-top:1px solid #3f7fc0}
.nav-item{top:0;height:48px;line-height:48px;font-family:"Noto Serif",Georgia,serif;font-size:14.5px;color:var(--white);text-align:center}
.nav-item.active{color:var(--brand-dark)}
.nav-divider{top:0;width:1px;height:48px;background:#3a78bb}

/* hero */
.hero{left:0;top:184px;width:1134px;height:310px;background:linear-gradient(180deg,#8ab6dc 0%,#b9cfe0 35%,#9a8a78 70%,#6f6558 100%)}

/* about */
.about-title{left:91px;top:536px;font-size:28px;color:var(--ink)}
.about-rule{left:91px;top:584px;width:582px;height:1px;background:var(--rule)}
.about-accent{left:91px;top:583px;width:70px;height:3px;background:var(--brand)}
.about-text{left:91px;top:606px;width:585px;font-family:Arial,Helvetica,sans-serif;font-size:14.3px;line-height:22.6px;color:#333}
.about-photo{left:734px;top:581px;width:311px;height:198px;border:5px solid #cbcbcb;background:linear-gradient(135deg,#f4f5f6 0%,#dfe4ea 55%,#2f4b68 80%,#e9ecef 100%)}

/* footer */
.footer{left:0;top:823px;width:1134px;height:340px;background:var(--map)}
.contact-title{left:94px;top:841px;font-size:21px;color:var(--white)}
.contact-rule{left:94px;top:873px;width:318px;border-top:1px dashed #8a8a8a}
.contact-item{left:126px;font-family:Arial,Helvetica,sans-serif;font-size:14px;line-height:19.5px;color:var(--white)}
.contact-icon{left:92px}
.footer-mark{left:472px;top:919px;width:100px;height:100px;border-radius:50%;background:#2f4a6c;border:2px solid #4c6585}
.footer-name{left:473px;top:1030px;color:#9aa0a6;line-height:1}
.footer-name .l1{display:block;font-size:24px}
.footer-name .l2{display:block;font-size:13px;margin-top:3px}

.inquiry{left:730px;top:842px;width:296px;height:308px;background:var(--panel);border-top:2px solid #c9ced3}
.inquiry-icon{left:744px;top:857px;width:39px;height:39px;border-radius:50%;background:var(--white)}
.inquiry-title{left:796px;top:860px;font-size:26px;color:var(--white)}
.inquiry-lede{left:743px;top:914px;font-family:Arial,Helvetica,sans-serif;font-size:13px;color:var(--white)}
.field{left:743px;width:270px;height:32px;background:var(--field);color:#e9e9e9;font-family:Arial,Helvetica,sans-serif;font-size:13px;padding:9px 11px}
.submit{left:743px;top:1099px;width:113px;height:31px;background:var(--brand);color:var(--white);font-family:Arial,Helvetica,sans-serif;font-weight:700;font-size:16px;text-align:center;line-height:31px;letter-spacing:.5px}

.copyright{left:0;top:1163px;width:1134px;height:37px;background:var(--bar);color:var(--white);font-family:Arial,Helvetica,sans-serif;font-size:12.5px;text-align:center;line-height:37px}
</style>
</head>
<body>

<header class="abs header">
  <div class="abs side-band" style="left:0;width:120px"></div>
  <div class="abs side-band" style="left:1054px;width:80px"></div>
  <div class="abs brand-mark"></div>
  <div class="abs brand-name"><span class="l1">Tallow Ridge</span><span class="l2">COMMUNICATION SOLUTIONS</span></div>

  <div class="abs follow">Follow Us On</div>
  <div class="abs social" style="left:931px"></div>
  <div class="abs social" style="left:969px"></div>
  <div class="abs social" style="left:1008px"></div>

  <svg class="abs" style="left:644px;top:68px" width="46" height="50" viewBox="0 0 46 50" aria-hidden="true">
    <rect x="8" y="4" width="30" height="38" fill="#fff" stroke="#0455a3" stroke-width="2"/>
    <rect x="0" y="6" width="22" height="10" fill="#fff" stroke="#0455a3" stroke-width="1.5"/>
    <text x="3" y="14.5" font-size="8" font-family="Arial" font-weight="700" fill="#0455a3">PDF</text>
    <path d="M23 20v12M18 27l5 5 5-5M16 36h14" fill="none" stroke="#0455a3" stroke-width="1.6"/>
    <path d="M4 44h40" stroke="#0455a3" stroke-width="3"/>
  </svg>
  <div class="abs brochure-btn cond">Download Our Brochure</div>

  <svg class="abs" style="left:886px;top:79px" width="30" height="30" viewBox="0 0 30 30" aria-hidden="true">
    <circle cx="15" cy="15" r="13.5" fill="none" stroke="#0455a3" stroke-width="1.6"/>
    <path d="M11 8c-2 1-3 3-2 6 1 4 4 7 8 9 2 1 4 0 5-2l-3-3-2 1c-2-1-4-3-5-5l1-2z" fill="#0455a3"/>
  </svg>
  <div class="abs call-label">Call Us Today</div>
  <div class="abs call-number">123-456-7890</div>
</header>

<nav class="abs nav">
  <div class="abs nav-item active" style="left:80px;width:98px">About Us</div>
  <div class="abs nav-divider" style="left:178px"></div>
  <div class="abs nav-item" style="left:178px;width:221px">Phone Systems &amp; Services</div>
  <div class="abs nav-divider" style="left:399px"></div>
  <div class="abs nav-item" style="left:399px;width:233px">Low Voltage Cabling Service</div>
  <div class="abs nav-divider" style="left:632px"></div>
  <div class="abs nav-item" style="left:632px;width:149px">Carrier Services</div>
  <div class="abs nav-divider" style="left:781px"></div>
  <div class="abs nav-item" style="left:781px;width:280px">Video Surveillance Systems Service</div>
</nav>

<div class="abs hero" role="img" aria-label="Security camera in front of a city skyline"></div>

<main>
  <h1 class="abs about-title cond" style="font-weight:400">About Us</h1>
  <div class="abs about-rule"></div>
  <div class="abs about-accent"></div>
  <p class="abs about-text">Tallow Ridge is a communications company based in Phoenix, providing a host of services to customers of all sizes, industries, and professions. We pride ourselves on having a great professional relationship with each of our clients. This allows us to truly understand our customer’s needs. Our key service concept is to relieve the customer of any worries relating to telecom/IT by reducing their over-all costs, and provide a reliable and comprehensive communication solution. Our team has worked together for nearly 10 years and is cohesive in our approach in exceeding our customer’s expectations</p>
  <div class="abs about-photo" role="img" aria-label="Office worker at a laptop"></div>
</main>

<footer>
  <div class="abs footer" role="img" aria-label="Street map of the office area"></div>

  <h2 class="abs contact-title cond" style="font-weight:400">Contact Details</h2>
  <div class="abs contact-rule"></div>

  <svg class="abs contact-icon" style="top:888px" width="18" height="22" viewBox="0 0 18 22" aria-hidden="true"><path d="M9 1a7 7 0 0 0-7 7c0 5 7 13 7 13s7-8 7-13a7 7 0 0 0-7-7z" fill="#fff"/><circle cx="9" cy="8" r="2.6" fill="#3d3f42"/></svg>
  <div class="abs contact-item" style="top:886px">Postal Address<br>Street Name, City Name State Zipcode</div>

  <svg class="abs contact-icon" style="top:940px" width="18" height="20" viewBox="0 0 18 20" aria-hidden="true"><path d="M4 1c-3 2-3 5-2 8 2 5 5 8 9 10 2 1 4 0 5-2l-3-4-3 1c-2-1-4-4-4-6l2-2z" fill="#fff"/></svg>
  <div class="abs contact-item" style="top:938px">Telephone<br>123-456-7890 &amp; Fax: 456-789-4560</div>

  <svg class="abs contact-icon" style="top:997px" width="18" height="13" viewBox="0 0 18 13" aria-hidden="true"><rect width="18" height="13" fill="#fff"/><path d="M0 0l9 7 9-7" fill="none" stroke="#3d3f42" stroke-width="1.5"/></svg>
  <div class="abs contact-item" style="top:991px">Email<br>Information and Support: inquiry@tallowridgecs.com</div>

  <svg class="abs contact-icon" style="top:1045px" width="18" height="18" viewBox="0 0 18 18" aria-hidden="true"><circle cx="9" cy="9" r="8" fill="#fff"/></svg>
  <div class="abs contact-item" style="top:1043px">Social Page<br>www.socialpage.com/tallowridgesolutions</div>

  <svg class="abs contact-icon" style="top:1101px" width="18" height="18" viewBox="0 0 18 18" aria-hidden="true"><rect x="1" y="1" width="16" height="16" rx="3" fill="#fff"/></svg>
  <div class="abs contact-item" style="top:1098px">Photo Stream<br>www.photostream.com/tallowridgesolutions</div>

  <div class="abs footer-mark"></div>
  <div class="abs footer-name"><span class="l1">Tallow Ridge</span><span class="l2">COMMUNICATION SOLUTIONS</span></div>

  <form class="abs inquiry" aria-label="Quick Inquiry"></form>
  <div class="abs inquiry-icon"></div>
  <svg class="abs" style="left:753px;top:866px" width="22" height="22" viewBox="0 0 22 22" aria-hidden="true"><path d="M6 2C3 4 2 7 4 11c2 4 5 7 9 9 3 1 5 0 6-2l-4-4-3 1c-2-1-4-3-5-5l1-3z" fill="#0455a3"/></svg>
  <h2 class="abs inquiry-title cond" style="font-weight:400">Quick Inquiry</h2>
  <p class="abs inquiry-lede">Lorem ipsum dolor sit amet, consectetuer</p>
  <div class="abs field" style="top:938px">Name</div>
  <div class="abs field" style="top:974px">Email</div>
  <div class="abs field" style="top:1009px">Phone</div>
  <div class="abs field" style="top:1044px;height:40px;padding-top:8px">Message</div>
  <div class="abs submit">SUBMIT</div>

  <div class="abs copyright">Copyright© 2016&nbsp; Tallow Ridge Communication Solutions&nbsp; All Rights Reserved</div>
</footer>

</body>
</html>
```